Design a Google site for a travel agency

I own a travel agency and I would like to have a Google site built for my company called Harborquestjourneys.com by Bright Path Holidays. Our specialty Cruising and adventure. We create a lot of custom tour of Europe and Peru. Our Adventure tours targets mainly women from 25 to 65. I would like to site especially the cruise to appeal to family but also upscale more expensive upscale clientele.
Updates

I would like to shift away from create a new site with multiple pages to one simple Google Site page with a Contact us page and testimonials. The sites theme is Cruise & Adventure Travel. We specialize in selling cruises and building custom travel tours around the world.

Target Market(s)

Cruisers and adventure travelers for women from 25 to 70

Industry/Entity Type

travel industry with a focus on cruising and adventure travel

Coding

Coded - Design and coding required

Number of Pages Required

5+ page

Font styles to use
Serif
Sans Serif

Requirements
Must have
• Home page, Cruise, Adventure Tours, Testimonials, About Us
Nice to have
• Auto place https://www.brightpathholidays.ca/offers into the site.
Should not have
• beach resorts

```html
<!DOCTYPE html>
<html lang="en">
<head>
<meta charset="utf-8">
<title>Harborquestjourneys.com – Harbor Quest Journeys</title>
<link href="https://fonts.googleapis.com/css2?family=Poppins:wght@300;400;500;600;700&family=Open+Sans:wght@400;600&display=swap" rel="stylesheet">
<style>
:root{
  --black:#000;
  --white:#fff;
  --ink:#1c1c1c;
  --muted:#444;
  --cream:#f7f5f1;
  --teal:#2a9bb0;
  --green:#2e7d4f;
  --orange:#e9771f;
  --blue:#1b7fae;
  --line:#bdbdbd;
  --mint:#8fd6c8;
}
*{box-sizing:border-box;margin:0;padding:0}
html,body{width:1200px;height:4181px;overflow:hidden}
body{position:relative;background:var(--white);font-family:"Open Sans",sans-serif;color:var(--ink)}
.abs{position:absolute}
.header{left:0;top:0;width:1200px;height:105px;background:var(--black)}
.brand{left:36px;top:36px;font:600 17px "Poppins",sans-serif;color:var(--white)}
.nav{right:190px;top:62px;display:flex;gap:24px;font:500 16px "Poppins",sans-serif;color:var(--white)}
.nav .active{color:var(--mint)}
.nav-btn{left:1030px;top:53px;width:134px;height:34px;border:2px solid var(--white);border-radius:18px;color:var(--white);font:600 12px "Poppins",sans-serif;display:flex;align-items:center;justify-content:center}
.hero{left:0;top:105px;width:1200px;height:723px;background:linear-gradient(180deg,#a9c3cf 0%,#6f8a8c 25%,#3d6c7a 50%,#2c5f74 70%,#4e7a3c 100%)}
.hero-title{left:276px;top:246px;font:700 64px/62px "Poppins",sans-serif;color:var(--white);white-space:nowrap}
.search{left:235px;top:401px;width:733px;height:67px;background:var(--white);border-radius:34px}
.search span{position:absolute;left:42px;top:21px;font:400 21px "Poppins",sans-serif;color:var(--ink)}
.search b{position:absolute;right:18px;top:12px;width:162px;height:43px;border-radius:22px;background:var(--teal);color:var(--white);font:600 15px "Poppins",sans-serif;display:flex;align-items:center;justify-content:center}
.chat{left:1030px;top:460px;width:154px;height:43px;background:var(--teal);color:var(--white);font:400 14px "Poppins",sans-serif;display:flex;align-items:center;padding-left:20px;gap:10px}
.chat i{width:20px;height:20px;border-radius:50%;border:2px solid var(--white)}
.h2{font:400 28px "Poppins",sans-serif;color:var(--ink);white-space:nowrap}
.tile{overflow:hidden}
.tile-text{position:absolute;font:700 72px/76px "Poppins",sans-serif;color:var(--white)}
.plan{left:800px;top:1462px;width:246px;height:235px;background:var(--orange)}
.plan span{position:absolute;left:18px;top:28px;font:700 39px/43px "Poppins",sans-serif;color:var(--white)}
.dot{width:31px;height:31px;border-radius:50%;background:var(--orange)}
.pill{height:42px;border-radius:21px;background:var(--green);color:var(--white);font:500 13px "Poppins",sans-serif;display:flex;align-items:center;justify-content:center}
.cream{background:var(--cream)}
.step-num{font:400 14px "Poppins",sans-serif;color:var(--green)}
.step-title{font:400 42px "Poppins",sans-serif;color:var(--ink)}
.step-text{font:400 13.5px/23px "Open Sans",sans-serif;color:var(--muted);width:340px}
.circle{width:231px;height:231px;border-radius:50%}
.footer-name{left:63px;top:3852px;font:600 19px "Poppins",sans-serif}
.contact-row{left:72px;display:flex;align-items:center;gap:18px;font:400 13.5px/22px "Open Sans",sans-serif;color:var(--ink)}
.contact-row .ico{width:34px;height:34px;border-radius:50%;background:var(--black);display:flex;align-items:center;justify-content:center;flex:none}
.social{width:26px;height:26px;border-radius:50%}
.fnav{left:502px;width:195px;font:400 11px "Poppins",sans-serif;text-align:center;color:var(--ink)}
.fnav.active{background:var(--blue);color:var(--white);height:39px;line-height:39px;font-weight:600}
.form-title{left:874px;top:3856px;font:400 21px "Poppins",sans-serif}
.lbl{font:400 8px "Open Sans",sans-serif;color:var(--muted)}
.field{border-bottom:1px solid var(--line);height:22px}
.msg{left:874px;top:4000px;width:266px;height:50px;background:var(--cream);border-bottom:1px solid var(--line)}
.submit{left:874px;top:4066px;width:86px;height:28px;border-radius:14px;background:var(--teal);color:var(--white);font:600 14px "Poppins",sans-serif;display:flex;align-items:center;justify-content:center}
</style>
</head>
<body>

<header class="abs header">
  <div class="abs brand">Bright Path Holidays</div>
  <nav class="abs nav"><span class="active">Home</span><span>Cruises</span><span>Adventures Tours</span><span>Testimonials</span><span>More</span></nav>
  <div class="abs nav-btn">Check Availability</div>
</header>

<section class="abs hero" role="img" aria-label="Fjord with cruise ships between green mountains"></section>
<h1 class="abs hero-title">Harbor Quest<br>Journeys</h1>
<div class="abs search"><span>Travel The Way You Want It</span><b>Check Availability</b></div>
<div class="abs chat"><i></i>Let's Chat!</div>

<h2 class="abs h2" style="left:47px;top:918px">Why Book With Us</h2>

<div class="abs tile" style="left:31px;top:1145px;width:370px;height:552px;background:linear-gradient(180deg,#f4f2ee 0%,#f4f2ee 18%,#8a8a78 19%,#7a5a4a 60%,#3c3b38 100%)" role="img" aria-label="Traveler beside a vintage van under hot air balloons"></div>
<div class="abs tile-text" style="left:60px;top:1285px">Long<br>voyage</div>

<div class="abs tile" style="left:416px;top:1145px;width:368px;height:552px;background:linear-gradient(180deg,#3f8f96 0%,#4c9aa0 17%,#f0a94a 20%,#d99a55 45%,#3d8fa5 70%,#f2a54c 90%,#e8a258 100%)" role="img" aria-label="Sea sunset collage with pier ladder"></div>
<div class="abs tile-text" style="left:448px;top:1358px">Find<br>yourself</div>

<div class="abs tile" style="left:781px;top:1145px;width:245px;height:304px;background:linear-gradient(180deg,#7fa7cf 0%,#d9e2ea 45%,#1f4f86 100%)" role="img" aria-label="Cruise ship bow at sea"></div>
<div class="abs" style="left:820px;top:1188px;font:400 33px/40px 'Poppins',sans-serif;color:var(--white)">Trip<br>Advice</div>

<div class="abs plan"><span>Plan Your<br>Trip With<br>Us</span></div>

<div class="abs dot" style="left:393px;top:1786px"></div>
<div class="abs h2" style="left:442px;top:1781px">Get to Know Us</div>
<div class="abs pill" style="left:669px;top:1780px;width:136px">Learn More</div>

<section class="abs cream" style="left:0;top:1908px;width:1200px;height:853px"></section>
<h2 class="abs h2" style="left:0;width:1200px;text-align:center;top:2025px">Book Your Trip in 3 Easy Steps</h2>

<div class="abs step-num" style="left:127px;top:2170px">01</div>
<div class="abs step-title" style="left:125px;top:2195px">Reserve Your Ride</div>
<p class="abs step-text" style="left:127px;top:2252px">I'm a paragraph. Click here to add your own text and edit me. Let your users get to know you.</p>

<div class="abs step-num" style="left:127px;top:2353px">02</div>
<div class="abs step-title" style="left:125px;top:2378px">Plan Your Trip</div>
<p class="abs step-text" style="left:127px;top:2435px">I'm a paragraph. Click here to add your own text and edit me. Let your users get to know you.</p>

<div class="abs step-num" style="left:127px;top:2540px">03</div>
<div class="abs step-title" style="left:125px;top:2565px">Hit the Road</div>
<p class="abs step-text" style="left:127px;top:2622px">I'm a paragraph. Click here to add your own text and edit me. Let your users get to know you.</p>

<div class="abs" style="left:744px;top:2183px;width:346px;height:536px;background:linear-gradient(180deg,#2e9aaa 0%,#5d8fa0 40%,#2f6b7c 70%,#c09a3a 100%)" role="img" aria-label="Paraglider over misty mountains"></div>
<div class="abs" style="left:648px;top:2192px;width:237px;height:236px;background:linear-gradient(90deg,#e6e6e6 0%,#cfcfcf 55%,#6b6b6b 100%)" role="img" aria-label="Traveler stepping out of a camper van door"></div>

<div class="abs circle" style="left:-173px;top:2769px;background:#e2c9a1" role="img" aria-label="Desert dunes"></div>
<div class="abs circle" style="left:59px;top:2769px;background:radial-gradient(circle,#f4f4f4 40%,#dcdcdc 100%)" role="img" aria-label="Portrait under a wide white hat"></div>
<div class="abs circle" style="left:314px;top:2769px;background:radial-gradient(circle,#4f8a6a 0%,#1f4a36 100%)" role="img" aria-label="Striped tropical leaves"></div>
<div class="abs circle" style="left:569px;top:2769px;background:linear-gradient(135deg,#e9e4df 0%,#d8aa97 50%,#b9c7d2 100%)" role="img" aria-label="Pastel apartment building facade"></div>
<div class="abs circle" style="left:824px;top:2769px;background:linear-gradient(180deg,#f1e3d0 0%,#e2bd8d 100%)" role="img" aria-label="Desert sand dunes"></div>
<div class="abs circle" style="left:1079px;top:2769px;background:#ececec" role="img" aria-label="Portrait under a wide white hat"></div>
<svg class="abs" style="left:1152px;top:2866px" width="22" height="36" viewBox="0 0 22 36"><path d="M4 4 L18 18 L4 32" fill="none" stroke="#fff" stroke-width="3"/></svg>

<section class="abs cream" style="left:0;top:3029px;width:1200px;height:214px"></section>
<div class="abs dot" style="left:321px;top:3119px"></div>
<div class="abs h2" style="left:369px;top:3114px">Find Your Next Road Trip</div>
<div class="abs pill" style="left:716px;top:3113px;width:163px">Discover Trip Ideas</div>

<section class="abs" style="left:0;top:3243px;width:1200px;height:427px;background:linear-gradient(135deg,#37c3c9 0%,#1fb1b8 50%,#3ccad0 100%)" role="img" aria-label="Aerial view of a river cruise ship on turquoise water"></section>

<div class="abs" style="left:63px;top:3760px;font:600 18px 'Poppins',sans-serif;color:var(--orange)">Bright Path Holidays</div>
<div class="abs footer-name">HARBOR QUEST JOURNEYS</div>

<div class="abs contact-row" style="top:3924px">
  <span class="ico"><svg width="16" height="18" viewBox="0 0 16 18"><path d="M8 17 C3 11 2 9 2 7 A6 6 0 0 1 14 7 C14 9 13 11 8 17Z" fill="none" stroke="#fff" stroke-width="1.6"/><circle cx="8" cy="7" r="2" fill="none" stroke="#fff" stroke-width="1.4"/></svg></span>
  <span>14 Lantern Quay Rd, Seabrook, NB E2K 4T8,<br>Canada</span>
</div>
<div class="abs contact-row" style="top:3994px">
  <span class="ico"><svg width="18" height="14" viewBox="0 0 18 14"><rect x="1" y="1" width="16" height="12" rx="1.5" fill="none" stroke="#fff" stroke-width="1.6"/><path d="M1 2 L9 8 L17 2" fill="none" stroke="#fff" stroke-width="1.6"/></svg></span>
  <span>hello@harborquestjourneys.com</span>
</div>
<div class="abs contact-row" style="top:4067px">
  <span class="ico"><svg width="16" height="16" viewBox="0 0 16 16"><path d="M3 1 L6 4 L4.5 6.5 C5.5 8.5 7.5 10.5 9.5 11.5 L12 10 L15 13 L13 15 C7 15 1 9 1 3 Z" fill="none" stroke="#fff" stroke-width="1.4"/></svg></span>
  <span>506-555-0147</span>
</div>
<div class="abs social" style="left:72px;top:4134px;background:#1f6fd6"></div>
<div class="abs social" style="left:123px;top:4134px;background:#2a9de8"></div>
<div class="abs social" style="left:174px;top:4134px;background:#c7377e"></div>

<div class="abs pill" style="left:505px;top:3735px;width:166px;height:41px;background:var(--orange);font-weight:600;font-size:14px">Check Availability</div>
<div class="abs fnav active" style="top:3859px">Home</div>
<div class="abs fnav" style="top:3922px">Cruises</div>
<div class="abs fnav" style="top:3973px">Adventures Tours</div>
<div class="abs fnav" style="top:4025px">Testimonials</div>
<div class="abs fnav" style="top:4075px">About</div>

<div class="abs form-title">Contact Us</div>
<div class="abs lbl" style="left:874px;top:3890px">First Name</div>
<div class="abs field" style="left:874px;top:3902px;width:127px"></div>
<div class="abs lbl" style="left:1013px;top:3890px">Last Name</div>
<div class="abs field" style="left:1013px;top:3902px;width:127px"></div>
<div class="abs lbl" style="left:874px;top:3936px">Email *</div>
<div class="abs field" style="left:874px;top:3948px;width:127px"></div>
<div class="abs lbl" style="left:1013px;top:3936px">Subject</div>
<div class="abs field" style="left:1013px;top:3948px;width:127px"></div>
<div class="abs lbl" style="left:874px;top:3984px">Message *</div>
<div class="abs msg"></div>
<div class="abs submit">Submit</div>

</body>
</html>
```